We want to design total new business card and logo for Kestrel Building Services Ltd

Our company name Kestrel Building Services Ltd. Design new logo and business card , need hi-end luxury style art for architecture and construction industry. The card should simple but stylish. Our business focus on CONNECT tradesman to construction company, help marketing construction company tender oversea projects, managing franchise in construction sector, delivery amazing services to our client, so Logo should show the LINKING TRADES, BUILDING PARTNERS, LUXURY. Visit our website for more information: kestrelgroup.example.nz

Target Market(s)

Directors or managers

Industry/Entity Type

Construction Company

Contact Information for Business Card

Name, Title, Mobile, Email, Website

Font styles to use
Serif

Colors

Designer to choose colors to be used in the design.

Requirements
Must have
• Simple and luxury, connection icon
Nice to have
• Special materials, plastic card, look through,...
• Look new ideas.

```html
<!DOCTYPE html>
<html lang="en">
<head>
<meta charset="utf-8">
<title>Kestrel Building Services Ltd — Business Card</title>
<link rel="stylesheet" href="https://fonts.googleapis.com/css2?family=Montserrat:wght@700&family=Open+Sans:wght@400;600&display=swap">
<style>
  :root {
    --page-bg: #e4e5e7;
    --brand-blue: #1d4fa6;
    --brand-navy: #1a3f95;
    --accent-sky: #3a9ad6;
    --card-white: #f7f7f7;
    --ink-grey: #505257;
    --rule-grey: #6b6d72;
  }
  * { box-sizing: border-box; margin: 0; padding: 0; }
  html, body { width: 1200px; height: 1021px; overflow: hidden; }
  body {
    background: var(--page-bg);
    font-family: "Open Sans", Arial, sans-serif;
    display: flex;
    flex-direction: column;
    align-items: center;
    justify-content: center;
    gap: 44px;
  }
  .card {
    width: 760px;
    height: 434px;
    border-radius: 4px;
    box-shadow: 0 6px 18px rgba(0,0,0,0.18);
    position: relative;
  }
  .card-back {
    background: var(--brand-blue);
    display: flex;
    flex-direction: column;
    align-items: center;
    justify-content: center;
    color: #fff;
  }
  .card-front {
    background: linear-gradient(120deg, #ececec 0%, var(--card-white) 60%, #fbfbfb 100%);
  }
  .brand {
    display: flex;
    flex-direction: column;
    align-items: center;
  }
  .brand-mark {
    width: 34px;
    height: 34px;
    margin-bottom: 18px;
  }
  .card-back .brand-mark { background: #fff; }
  .card-front .brand-mark { background: var(--brand-navy); }
  .brand-name {
    font-family: "Montserrat", Arial, sans-serif;
    font-weight: 700;
    font-size: 25px;
    letter-spacing: 0.2px;
    text-transform: uppercase;
    line-height: 1;
  }
  .card-front .brand-name { color: var(--brand-navy); }
  .brand-tagline {
    font-size: 17px;
    margin-top: 6px;
    letter-spacing: 0.3px;
  }
  .card-front .brand-tagline { color: var(--ink-grey); }
  .card-front .brand {
    position: absolute;
    top: 70px;
    left: 0;
    right: 0;
  }
  .contact-block {
    position: absolute;
    top: 268px;
    left: 0;
    right: 0;
    display: flex;
    justify-content: center;
    align-items: stretch;
    gap: 26px;
  }
  .person {
    text-align: right;
    padding-top: 2px;
  }
  .person-name {
    color: var(--brand-navy);
    font-weight: 600;
    font-size: 23px;
  }
  .person-title {
    color: var(--ink-grey);
    font-size: 18px;
  }
  .divider {
    width: 1.5px;
    background: var(--rule-grey);
  }
  .contact-list {
    list-style: none;
    padding-top: 14px;
    color: var(--ink-grey);
    font-size: 18px;
    line-height: 1.35;
  }
  .contact-list li {
    display: flex;
    align-items: center;
    gap: 9px;
  }
  .contact-list svg {
    width: 16px;
    height: 16px;
    flex: none;
    fill: none;
    stroke: var(--accent-sky);
    stroke-width: 1.8;
  }
</style>
</head>
<body>

  <section class="card card-back" aria-label="Card back">
    <div class="brand">
      <span class="brand-mark" aria-hidden="true"></span>
      <p class="brand-name">Kestrel Building Services Ltd</p>
      <p class="brand-tagline">Linking Trades, Building Partners</p>
    </div>
  </section>

  <section class="card card-front" aria-label="Card front">
    <div class="brand">
      <span class="brand-mark" aria-hidden="true"></span>
      <p class="brand-name">Kestrel Building Services Ltd</p>
      <p class="brand-tagline">Linking Trades, Building Partners</p>
    </div>

    <div class="contact-block">
      <div class="person">
        <p class="person-name">Daniel Hartley</p>
        <p class="person-title">Managing Director</p>
      </div>
      <span class="divider" aria-hidden="true"></span>
      <ul class="contact-list">
        <li>
          <svg viewBox="0 0 16 16" aria-hidden="true"><path d="M4 1.5 L6.5 4.5 L5 6.5 Q6.5 9.5 9.5 11 L11.5 9.5 L14.5 12 L12.5 14.5 Q6 14 1.5 3.5 Z" style="fill:var(--accent-sky);stroke:none"/></svg>
          0210-555-0147
        </li>
        <li>
          <svg viewBox="0 0 16 16" aria-hidden="true"><rect x="1.5" y="3.5" width="13" height="9"/><path d="M1.5 3.5 L8 9 L14.5 3.5"/></svg>
          daniel@kestrelgroup.example.nz
        </li>
        <li>
          <svg viewBox="0 0 16 16" aria-hidden="true"><circle cx="8" cy="8" r="6.3"/><ellipse cx="8" cy="8" rx="2.8" ry="6.3"/><path d="M1.7 8 H14.3"/></svg>
          www.kestrelgroup.example.nz
        </li>
      </ul>
    </div>
  </section>

</body>
</html>
```